Wordpress Web Design & Coding for velcorahealth.ca

We need a website for a new investment company that is visually grabbing and vibrant. We would like to see a web page that displays trust, growth and confidence. Needs to be responsive and mobile friendly for all browsers and coded for both Android & IOS.

Open to the number of pages and menu items. I selected 4 but if you feel the layout would work better with less I am open to this. Need to sell the people (management team/related businesses) and then show where the invested money will be going (upcoming projects).

Company Info:

Vel Cora is an investment company put together by a group of seasoned business professionals who have come together to combine decades of success in the real estate development, management, financing and medical services. The company will be a full service company offering turn key solutions for medical professionals.

Vel-Cora will focus on providing a full range of services via a group of distinct companies to deliver newly emerging needs of the medical community. The end goal will be to create complete solutions for individuals in the medical community. Our group has experience and success with the conceptualization, construction and financing of medical and dental clinic spaces. Vel-Cora Solutions will be established to accommodate all areas of the development and creation of clinics for medical professionals from building construction to equipment financing and administrations.

You can mention these companies and take photos from their websites. You can also use stock photos.

Our construction partner:
https://318bld.com/projects/

Our equipment leasing partner:
https://www.norvixa.com/

Our Management Team and medical partners

Gil Parish
https://www.ourfirmstance.ca/

Dietmar Vellasquin
https://www.gshdentalservices.com/about-us

PROPOSED PROJECTS (see attachment for details)
Pinegrove Business Park
Holtmere Business Park
Mt. Corwin Ridge Professional

Target Market(s)

Investors

Industry/Entity Type

Investment

Coding

Coded - Design and coding required

Number of Pages Required

4 page

Font styles to use
Sans Serif

Requirements
Must have
• Wordpress – must be both desktop and mobile friendly with fast page load speed
Ability to edit after ourselves in Wordpress
Attractive home page with logo etc.
Logo colours are: for the blue the pantone color is #0355a3
and for the green is #8cc63f

Sections, about us, what we do/services we provide, contact us

```html
<!DOCTYPE html>
<html lang="en">
<head>
<meta charset="utf-8">
<title>Vel-Cora Solutions</title>
<link href="https://fonts.googleapis.com/css2?family=Montserrat:wght@400;500;600;700&family=Raleway:wght@700;800&family=Oswald:wght@500&display=swap" rel="stylesheet">
<style>
:root{
  --blue:#0355a3;
  --blue-dark:#024a8f;
  --green:#8cc63f;
  --text:#4a4a4a;
  --muted:#777;
  --pale:#eaf2fc;
  --line:#e2e2e2;
}
*{box-sizing:border-box;margin:0;padding:0}
html,body{width:1200px;height:3706px;overflow:hidden}
body{font-family:'Montserrat',sans-serif;color:var(--text);background:#fff;position:relative}
section,header,footer{position:absolute;left:0;width:1200px}
.abs{position:absolute}
.h-title{font-family:'Raleway',sans-serif;font-weight:800;color:var(--blue);font-size:30px;letter-spacing:.5px;text-transform:uppercase}
.h-title .accent{color:var(--green)}
.bar{width:38px;height:3px;background:var(--green)}

/* header */
.site-header{top:0;height:114px;background:#fff;border-bottom:1px solid #ddd}
.brand{left:144px;top:46px;display:flex;align-items:center;gap:10px}
.brand-mark{width:22px;height:22px;background:var(--green)}
.brand-name{font-family:'Montserrat',sans-serif;font-weight:700;font-size:24px;color:var(--blue);letter-spacing:.5px}
.contact-top{top:16px;right:141px;display:flex;gap:20px;font-size:13px;font-weight:600;color:#222;align-items:center}
.contact-top span{display:flex;align-items:center;gap:8px}
.ic{width:26px;height:26px;border-radius:50%;background:var(--green);display:inline-flex;align-items:center;justify-content:center}
.nav{top:72px;left:591px;display:flex;gap:0;font-size:13px;font-weight:600;color:#222}
.nav a{color:inherit;text-decoration:none;padding:0 13px 14px;letter-spacing:.3px}
.nav a.active{color:var(--blue);border-bottom:3px solid var(--blue)}
.nav a+a{margin-left:22px}

/* hero */
.hero{top:114px;height:459px;background:linear-gradient(180deg,#bcd3ee 0%,#c7d9f0 40%,#8d959e 70%,#5d6a55 100%)}
.hero-title{top:32px;width:100%;text-align:center;font-family:'Oswald',sans-serif;font-weight:500;font-size:20px;line-height:35px;color:#10203a}

/* about */
.about{top:573px;height:405px;text-align:center}
.about .h-title{top:72px;width:100%}
.about p{position:absolute;left:150px;width:900px;font-size:12.5px;line-height:23px;color:#555}
.about a{color:var(--blue)}
.btn{display:inline-block;background:var(--blue);color:#fff;font-weight:600;font-size:13px;border-radius:3px;text-decoration:none}
.about .btn{position:absolute;left:537px;top:299px;width:126px;height:35px;line-height:35px}

/* solutions */
.solutions{top:978px;height:820px}
.sol-band{top:0;left:0;width:1200px;height:219px;background:var(--green)}
.sol-band h2{position:absolute;top:72px;width:100%;text-align:center;font-family:'Raleway',sans-serif;font-weight:800;font-size:30px;color:#fff;letter-spacing:.5px}
.sol-band .bar{position:absolute;left:581px;top:118px;background:#fff}
.card{top:149px;width:424px}
.card .photo{width:424px;height:459px;border-radius:6px}
.card h3{margin-top:24px;font-family:'Montserrat',sans-serif;font-weight:700;font-size:20px;color:var(--blue);padding-left:2px}
.card p{margin-top:14px;font-size:12.5px;line-height:23px;color:#555;padding-left:2px}
.more{display:block;margin-top:14px;padding-left:5px;color:var(--green);font-weight:600;font-size:14px}

/* projects */
.projects{top:1798px;height:648px}
.projects .h-title{top:24px;width:100%;text-align:center}
.projects .bar{left:581px;top:72px}
.feature{left:141px;top:96px;width:446px}
.feature .photo{height:306px;background:linear-gradient(180deg,#6d8fc0,#c6d6ec 60%,#dfe8f4)}
.feature h3{margin-top:14px;font-weight:700;font-size:19px;color:var(--blue)}
.sub{font-size:12px;color:#777;margin-top:3px}
.feature p{margin-top:14px;font-size:12.5px;line-height:23px;color:#555;letter-spacing:.2px}
.meta{display:flex;justify-content:space-between;font-size:10.5px;color:#555;border-top:1px solid var(--line);padding-top:10px;margin-top:12px}
.meta span{display:flex;align-items:center;gap:6px}
.item{left:606px;width:452px;height:144px}
.item .photo{position:absolute;left:0;top:0;width:213px;height:144px}
.item .body{position:absolute;left:234px;top:16px;width:218px}
.item h4{font-weight:700;font-size:14px;color:var(--blue)}
.item .sub{font-size:11.5px;margin-top:2px}
.item p{font-size:11.5px;line-height:18px;color:#555;margin-top:6px;letter-spacing:.5px}
.item .meta{border:none;padding-top:0;margin-top:10px}
.arrow{width:34px;height:34px;border-radius:50%;background:#eee;display:flex;align-items:center;justify-content:center;top:318px}

/* people */
.people{top:2446px;height:593px;background:var(--pale)}
.people .h-title{top:80px;line-height:38px}
.people .bar{top:151px}
.pcard{top:176px;width:208px}
.pcard .photo{height:217px}
.pcard .label{height:56px;background:var(--blue);color:#fff;font-weight:700;font-size:16px;line-height:20px;display:flex;align-items:center;justify-content:center;text-align:center}
.plogo{top:470px;width:208px;text-align:center;font-size:18px;font-weight:500;color:#666;letter-spacing:1px}

/* newsletter */
.newsletter{top:3039px;height:294px;background:#fff;text-align:center}
.newsletter .h-title{top:72px;width:100%}
.newsletter .lead{top:136px;width:100%;font-size:14px;color:#222;font-weight:500}
.newsletter .lead2{top:155px;width:100%;font-size:14px;color:var(--blue)}
.field{left:311px;top:180px;width:453px;height:41px;border:1px solid #ccc;border-radius:3px;font-size:12.5px;color:#666;text-align:left;padding:12px 14px}
.newsletter .btn{position:absolute;left:776px;top:180px;width:113px;height:41px;line-height:41px}

/* footer */
.footer{top:3333px;height:322px;background:var(--blue);color:#fff}
.footer h5{font-size:13px;font-weight:600;color:var(--green);letter-spacing:.5px}
.links{list-style:none;margin-top:24px;font-size:11.5px;line-height:23px}
.links li::before{content:"»";margin-right:7px}
.vline{top:58px;width:1px;height:170px;background:rgba(255,255,255,.25)}
.crow{display:flex;gap:12px;margin-top:16px;font-size:12px;line-height:18px}
.crow b{font-weight:700;font-size:12px}
.crow .ic{flex:none}
.soc{display:flex;align-items:center;gap:14px;font-size:13px;margin-top:14px}
.soc .dot{width:30px;height:30px;border-radius:50%;background:#fff;opacity:.9}
.foot-brand{left:878px;top:120px;display:flex;align-items:center;gap:10px}
.foot-brand .brand-mark{width:26px;height:26px;background:#7fb0e2}
.foot-brand .brand-name{color:#9cc3ec;font-size:28px}
.copy{top:3655px;height:51px;background:var(--green);color:#fff;font-size:13px;text-align:center;line-height:51px}
.copy b{font-weight:700}
</style>
</head>
<body>

<header class="site-header">
  <div class="abs brand"><span class="brand-mark"></span><span class="brand-name">VEL-CORA SOLUTIONS</span></div>
  <div class="abs contact-top">
    <span><i class="ic"><svg width="13" height="13" viewBox="0 0 24 24"><path fill="#fff" d="M6.6 10.8a15 15 0 006.6 6.6l2.2-2.2c.3-.3.7-.4 1-.2 1.1.4 2.3.6 3.6.6.6 0 1 .4 1 1V20c0 .6-.4 1-1 1A17 17 0 013 4c0-.6.4-1 1-1h3.5c.6 0 1 .4 1 1 0 1.3.2 2.5.6 3.6.1.3 0 .7-.2 1z"/></svg></i>123.456.7890</span>
    <span><i class="ic"><svg width="13" height="13" viewBox="0 0 24 24"><rect x="3" y="6" width="18" height="12" rx="1" fill="none" stroke="#fff" stroke-width="2"/><path d="M3 7l9 6 9-6" fill="none" stroke="#fff" stroke-width="2"/></svg></i>support@velcorasol.com</span>
  </div>
  <nav class="abs nav"><a class="active" href="#">HOME</a><a href="#">ABOUT US</a><a href="#">WHAT WE DO</a><a href="#">CONTACT US</a></nav>
</header>

<section class="hero" role="img" aria-label="Rendering of a two-storey commercial building with several tenant storefronts, cars and trees">
  <h1 class="abs hero-title">Vel-Cora Is An Investment Company With Focus On Providing A Full Range Of<br>Services, For The Newly Emerging Needs Of The Medical Community</h1>
</section>

<section class="about">
  <h2 class="abs h-title">About <span class="accent">Vel-Cora Solutions</span></h2>
  <p style="top:133px"><a href="#">Vel-Cora</a> is an investment company put together by a group of seasoned business professionals who have come together to combine decades of success in the real estate development, management, financing and medical services. The company will be a full service company offering turnkey solutions for medical professionals.</p>
  <p style="top:208px">Vel-Cora will focus on providing a full range of services via a group of distinct companies to deliver newly emerging needs of the medical community. The end goal will be to create complete solutions for individuals in the medical community. Our group has experience and success with the conceptualization, construction and financing of medical and dental clinic spaces.</p>
  <a class="btn" href="#">Read More</a>
</section>

<section class="solutions">
  <div class="abs sol-band"><h2>VEL-CORA SOLUTION</h2><div class="bar"></div></div>
  <article class="abs card" style="left:141px">
    <div class="photo" role="img" aria-label="Hand touching a hexagon network of leasing icons" style="background:linear-gradient(135deg,#dfe8f3,#5b86c4 55%,#2a4f8c)"></div>
    <h3>LEASING OPERATIONS</h3>
    <p>Vel-Cora Solutions leasing divison will secure an investment portfolio comprised of equipment leases and other small business financing solutions across the Western Region.</p>
    <a class="more">Know More ➔</a>
  </article>
  <article class="abs card" style="left:635px">
    <div class="photo" role="img" aria-label="Open hand holding a glowing digital shield with a check mark" style="background:radial-gradient(circle at 50% 40%,#6fb7ec,#1c5fa8 50%,#0a2550)"></div>
    <h3>SECURITY MEASURES</h3>
    <p>Vel-Cora Solution leasing divison will implement a number of security measures which ensures investors are secure and returns are maximised over the elife of the investments.</p>
    <a class="more">Know More ➔</a>
  </article>
</section>

<section class="projects">
  <h2 class="abs h-title">Upcoming <span class="accent">Projects</span></h2>
  <div class="abs bar"></div>
  <div class="abs arrow" style="left:84px"><svg width="12" height="12" viewBox="0 0 12 12"><path d="M8 1L3 6l5 5" fill="none" stroke="#333" stroke-width="2"/></svg></div>
  <div class="abs arrow" style="left:1081px"><svg width="12" height="12" viewBox="0 0 12 12"><path d="M4 1l5 5-5 5" fill="none" stroke="#333" stroke-width="2"/></svg></div>
  <article class="abs feature">
    <div class="photo" role="img" aria-label="Empty bright industrial warehouse interior with a steel roof"></div>
    <h3>Pinegrove Business Park</h3>
    <div class="sub">Office and Light Industrial Building Project</div>
    <p>The Pinegrove Business Park in Holtmere, Coastal Province on Brennock Island, is presently under contract with partners that are controlled by individuals who form part of the...(+)</p>
    <div class="meta"><span>📅 Apr 10, 2020</span><span>💬 3 Comments</span></div>
  </article>
  <article class="abs item" style="top:96px">
    <div class="photo" role="img" aria-label="Historic stone office building facade" style="background:linear-gradient(180deg,#b9c8dc,#c9b9a0 45%,#6b5a48)"></div>
    <div class="body"><h4>Holtmere Business Park</h4>
      <p>The city of Holtmere is a core municipalpty in the Western Communities. It is currently...(+)</p>
      <div class="meta"><span>📅 Apr 10, 2020</span><span>💬 3 Comments</span></div></div>
  </article>
  <article class="abs item" style="top:264px">
    <div class="photo" role="img" aria-label="Silhouettes of business people against a city skyline" style="background:linear-gradient(180deg,#d8e6f4,#6b8fbf 55%,#2f4f7e)"></div>
    <div class="body" style="top:8px"><h4>Mt. Corwin Ridge Professional</h4><div class="sub">Professional Services Buildings</div>
      <p>Mt. Corwin Professional building will feature a repurposed building adjacent to Mt.Corwin Ridge in...(+)</p>
      <div class="meta"><span>📅 Apr 10, 2020</span><span>💬 3 Comments</span></div></div>
  </article>
  <article class="abs item" style="top:432px">
    <div class="photo" role="img" aria-label="Three colleagues in discussion at a table" style="background:linear-gradient(135deg,#e9eef3,#a7b3bf 50%,#4b4f58)"></div>
    <div class="body"><h4>Lorem Ipsum Dolor</h4>
      <p>Lorem ipsum dolor sit amn alamet commons consectetuer adipiscing elit lorem ipsum amet dolar... (+)</p>
      <div class="meta"><span>📅 Apr 10, 2020</span><span>💬 3 Comments</span></div></div>
  </article>
</section>

<section class="people">
  <h2 class="abs h-title" style="left:144px">Our<br><span class="accent">Partners</span></h2>
  <div class="abs bar" style="left:144px"></div>
  <h2 class="abs h-title" style="left:629px">Our Management Team<br><span class="accent">and Medical Partners</span></h2>
  <div class="abs bar" style="left:629px"></div>

  <div class="abs pcard" style="left:141px"><div class="photo" role="img" aria-label="White commercial building exterior under blue sky" style="background:linear-gradient(180deg,#9cbfe6,#f0f0f0 55%,#8a9a6a)"></div><div class="label">Construction<br>Partner</div></div>
  <div class="abs pcard" style="left:367px"><div class="photo" role="img" aria-label="Modern white professional building with dark windows" style="background:linear-gradient(180deg,#c7d7ea,#f2f2f2 50%,#7d8794)"></div><div class="label">Equipment<br>Leasing Partner</div></div>
  <div class="abs pcard" style="left:625px"><div class="photo" role="img" aria-label="Portrait of Gil Parish" style="background:linear-gradient(180deg,#6e6e70,#cfd0d2)"></div><div class="label">Gil Parish</div></div>
  <div class="abs pcard" style="left:850px"><div class="photo" role="img" aria-label="Portrait of Dietmar Vellasquin outdoors by the water" style="background:linear-gradient(180deg,#8fb4cf,#3f7fa6 60%,#b79a7c)"></div><div class="label">Dietmar<br>Vellasquin</div></div>

  <div class="abs plogo" style="left:141px">318 BUILDERS INC.</div>
  <div class="abs plogo" style="left:367px">NORVIXA</div>
  <div class="abs plogo" style="left:625px">firmstance</div>
  <div class="abs plogo" style="left:850px">GSH DENTAL</div>
</section>

<section class="newsletter">
  <h2 class="abs h-title">Subscribe to <span class="accent">our newsletter</span></h2>
  <div class="abs lead">Want to keep up to date with all our latest news and information?</div>
  <div class="abs lead2">Enter your email below to be added to our mailing list.</div>
  <div class="abs field">Enter your email address</div>
  <a class="btn" href="#">SUBSCRIBE</a>
</section>

<footer class="footer">
  <div class="abs" style="left:144px;top:72px">
    <h5>QUICK LINKS</h5>
    <ul class="links"><li>HOME</li><li>ABOUT US</li><li>WHAT WE DO</li><li>CONTACT US</li></ul>
  </div>
  <div class="abs vline" style="left:288px"></div>
  <div class="abs" style="left:340px;top:72px;width:260px">
    <h5>CONTACT DETAILS</h5>
    <div class="crow" style="margin-top:22px"><i class="ic"><svg width="12" height="12" viewBox="0 0 24 24"><path fill="#fff" d="M12 2a7 7 0 00-7 7c0 5 7 13 7 13s7-8 7-13a7 7 0 00-7-7zm0 9.5A2.5 2.5 0 1112 6a2.5 2.5 0 010 5.5z"/></svg></i><div><b>VEL-CORA SOLUTION</b><br>123, Building Name, Street<br>City, State 123456</div></div>
    <div class="crow"><i class="ic"><svg width="12" height="12" viewBox="0 0 24 24"><path fill="#fff" d="M6.6 10.8a15 15 0 006.6 6.6l2.2-2.2c.3-.3.7-.4 1-.2 1.1.4 2.3.6 3.6.6.6 0 1 .4 1 1V20c0 .6-.4 1-1 1A17 17 0 013 4c0-.6.4-1 1-1h3.5c.6 0 1 .4 1 1 0 1.3.2 2.5.6 3.6.1.3 0 .7-.2 1z"/></svg></i><div><b>Phone</b><br>123.456.7890</div></div>
    <div class="crow"><i class="ic"><svg width="12" height="12" viewBox="0 0 24 24"><rect x="5" y="9" width="14" height="8" fill="#fff"/><rect x="7" y="4" width="10" height="5" fill="#fff"/></svg></i><div><b>Fax</b><br>support@velcorasol.com</div></div>
  </div>
  <div class="abs vline" style="left:612px"></div>
  <div class="abs" style="left:663px;top:72px">
    <h5>FOLLOW US ON</h5>
    <div class="soc" style="margin-top:22px"><span class="dot"></span>Socialia</div>
    <div class="soc"><span class="dot"></span>Quipster</div>
    <div class="soc"><span class="dot"></span>Careerly</div>
  </div>
  <div class="abs foot-brand"><span class="brand-mark"></span><span class="brand-name">VEL-CORA</span></div>
</footer>
<div class="abs copy" style="left:0;width:1200px">Copyright © 2020 <b>VEL-CORA SOLUTION</b>. All Rights Reserved.</div>

</body>
</html>
```